Personal Trainer website design

We are working with a personal trainer to design a website. They offer their primary services: Diet Coaching, In-Person Coaching (workouts), and Remote Coaching.
Some sites we like: https://www.mirabelthorne.com, https://kavialune.com/en-us, https://corvexfit.co.uk
Thank you for taking the time to consider designing a website for us. We are web developers based in Stockton, CA USA. Most of our projects go through the same process. Understanding this process may help you win a project with us. We custom-code all of our websites in-house. We don’t have any requirements as to what tools you use for your design, but ask that you follow these guidelines.
IMAGES:
We ask that if you use any images, or icons in the design, have a link to the asset, so we can purchase the image/icon. Most of the designs we submit do not have the customer’s images on them unless they have some great images. Be creative; show us the feeling that you are trying to portray with your image choices. Use any royalty-free site you choose. We subscribe to Quillon and mostly use their images, but are ok to purchase images outside of Quillon.
FONTS:
We ask that you identify the fonts you’re using in the design. This can be done in a message if you want. We typically use Brivane Fonts and Quillon Fonts.
CONTENT:
We're always open to different content and ideas. Often, we submit designs with stock images so that the client can see our vision. We typically go back and take pictures after the website launch to use their images with our vision. Lorem Ipsum is fine for paragraphs, but we ask that you make the Headers with correct English. We want to be able to show the vision and identify the sections of the website.
INSPIRATION:
We try and add a couple of links in the brief of some websites that we like to help you get started in your design.
REVISIONS:
We do not often ask for revisions of the designs unless we see something in the design that may not appeal to the client. If there are slight changes that we want to make, we simply do that in the development process.
FEEDBACK:
We rarely give feedback on designs during the design process. We are working on many website projects and do not have the time to give feedback. We usually respond if your request is well thought out and asks specific questions, but a note asking “feedback, please” usually goes unanswered.
1 page

```html
<!DOCTYPE html>
<html lang="en">
<head>
<meta charset="utf-8">
<title>Orbifit – Personal Training</title>
<link rel="stylesheet" href="https://fonts.googleapis.com/css2?family=Exo+2:wght@500;700;800&family=Poppins:wght@400;500;600&display=swap">
<style>
:root{
  --olive:#7b8c12;
  --olive-dark:#5f6e0a;
  --ink:#1b1b1b;
  --dark:#1f1f1f;
  --text:#3a3a3a;
  --muted:#8a8a8a;
  --light:#f1f1f1;
  --white:#ffffff;
  --star:#f2a516;
}
*{margin:0;padding:0;box-sizing:border-box}
html,body{width:1200px;height:3368px;overflow:hidden;background:var(--white)}
body{font-family:"Poppins",sans-serif;color:var(--text);position:relative}
.page{position:relative;width:1200px;height:3368px;overflow:hidden}
.abs{position:absolute}
.heading{font-family:"Exo 2",sans-serif;font-weight:800;color:var(--ink);text-transform:uppercase;letter-spacing:1px}
.mark{width:44px;height:44px;border-radius:50%;background:var(--olive);margin:0 auto}
.btn{display:inline-block;font-family:"Poppins",sans-serif;font-weight:600;font-size:15px;text-transform:uppercase;border-radius:30px;padding:15px 34px}
.btn-olive{background:var(--olive-dark);color:var(--white)}
.btn-white{background:var(--white);color:var(--ink)}

/* top bar */
.topbar{top:0;left:0;width:1200px;height:48px;background:var(--white);display:flex;align-items:center;padding:0 80px 0 110px;font-size:14px;font-weight:600;color:var(--ink);z-index:5}
.topbar .follow{color:var(--olive);margin-right:12px}
.topbar .soc{width:22px;height:22px;border-radius:50%;background:var(--olive);margin-right:8px}
.topbar .info{display:flex;align-items:center;margin-left:auto;gap:40px}
.topbar .info span{display:flex;align-items:center;gap:10px}
.icon-dot{width:28px;height:28px;border-radius:50%;background:var(--ink);display:flex;align-items:center;justify-content:center}
.topbar .follow-wrap{display:flex;align-items:center}

/* nav */
.nav{top:48px;left:0;width:1200px;height:100px;background:rgba(255,255,255,.96);display:flex;align-items:center;padding:0 110px;z-index:5}
.brand{display:flex;align-items:center;gap:10px;font-family:"Exo 2",sans-serif;font-weight:800;font-size:34px;color:var(--ink);text-transform:uppercase}
.brand i{width:26px;height:26px;border-radius:50%;background:var(--olive);display:block}
.menu{margin-left:auto;display:flex;align-items:center;gap:42px;font-size:16px;font-weight:500;color:var(--ink)}
.menu .active{background:var(--olive-dark);color:var(--white);padding:8px 20px;border-radius:20px}
.menu .cta{background:var(--olive-dark);color:var(--white);padding:12px 26px;border-radius:24px;font-weight:600}

/* hero */
.hero-photo{top:0;left:0;width:1200px;height:640px;background:linear-gradient(90deg,#f4f1ec 0%,#e9dfd4 35%,#bfa894 60%,#6d6a66 100%)}
.hero-copy{top:250px;left:110px;width:420px}
.hero-copy .eyebrow{font-family:"Exo 2",sans-serif;font-weight:800;font-size:28px;color:var(--ink);letter-spacing:2px}
.hero-copy h1{font-size:82px;line-height:1;margin:6px 0 16px}
.hero-copy p{font-size:15px;line-height:1.5;color:var(--text);margin-bottom:26px}
.dots{display:flex;gap:8px;margin-top:22px}
.dots b{width:9px;height:9px;border-radius:50%;background:#c6c6c6}
.dots b.on{background:var(--olive-dark)}

/* services */
.services{top:660px;left:0;width:1200px;text-align:center}
.services h2{font-size:44px;margin-top:14px}
.svc{position:absolute;border-radius:50%;overflow:hidden}
.svc-side{width:270px;height:300px;top:820px}
.svc-label{position:absolute;top:1140px;width:270px;text-align:center;font-size:19px;font-weight:500;color:var(--ink)}
.svc-main{top:768px;left:412px;width:400px;height:400px;border:10px solid var(--olive);background:linear-gradient(160deg,#8a9cb0,#3a4a5c)}
.svc-main .cap{position:absolute;left:0;right:0;top:215px;text-align:center;color:var(--white);padding:0 70px}
.svc-main .cap h3{font-family:"Exo 2",sans-serif;font-weight:800;font-size:22px;text-transform:uppercase}
.svc-main .cap p{font-size:12px;line-height:1.45;margin:8px 0 14px;opacity:.9}
.svc-main .cap a{font-size:14px;font-weight:600;border-bottom:2px solid var(--white);padding-bottom:2px}

/* about */
.about-bg{top:1200px;left:0;width:1200px;height:640px}
.about-art{top:1380px;left:140px;width:300px;height:300px;border-radius:50%;background:radial-gradient(circle at 45% 40%,#ffffff 0%,#e6e6e6 55%,#7b8c12 56%,#7b8c12 100%)}
.about-flag{top:1290px;left:300px;width:150px;height:150px;background:linear-gradient(135deg,#8c9d1c,#5f6e0a);border-radius:4px 40px 4px 4px}
.about-copy{top:1380px;left:590px;width:540px;color:#d8d8d8}
.about-copy .mark{margin:0 0 14px 0}
.about-copy h2{font-size:44px;color:var(--white);margin-bottom:18px}
.about-copy p{font-size:14px;line-height:1.65;margin-bottom:18px}

/* testimonials */
.reviews{top:1840px;left:0;width:1200px;text-align:center}
.reviews h2{font-size:44px;margin-top:14px}
.avatar{position:absolute;border-radius:50%;background:linear-gradient(160deg,#d8c3ae,#8f7561)}
.av-main{top:1945px;left:528px;width:144px;height:144px;border:6px solid var(--olive)}
.av-left{top:2015px;left:120px;width:70px;height:70px}
.av-right{top:1948px;left:995px;width:52px;height:52px}
.dot-red{position:absolute;width:12px;height:12px;border-radius:50%;background:#6e1a1a}
.review-body{position:absolute;top:2110px;left:0;width:1200px;text-align:center}
.review-body .name{font-family:"Exo 2",sans-serif;font-weight:700;font-size:21px;color:var(--ink)}
.review-body .loc{font-size:12px;color:var(--muted);margin-top:4px}
.stars{display:flex;gap:6px;justify-content:center;margin:14px 0 18px}
.review-body p{font-size:14px;line-height:1.6;width:640px;margin:0 auto;color:var(--text)}
.quote{position:absolute;font-family:"Exo 2",sans-serif;font-weight:800;font-size:230px;color:#d9d9d9;line-height:1}
.rv-dots{position:absolute;top:2312px;left:0;width:1200px;display:flex;justify-content:center}

/* contact */
.contact-bg{top:2360px;left:0;width:1200px;height:600px}
.contact-head{top:2420px;left:0;width:1200px;text-align:center}
.contact-head h2{font-size:44px;margin-top:14px}
.addr{top:2568px;left:112px;width:340px}
.addr h4{font-family:"Exo 2",sans-serif;font-weight:800;font-size:19px;color:var(--ink);margin-bottom:20px}
.addr .row{display:flex;gap:16px;margin-bottom:26px}
.addr .row .icon-dot{width:42px;height:42px;flex:none}
.addr .row strong{display:block;font-family:"Exo 2",sans-serif;font-weight:800;font-size:15px;color:var(--ink);text-transform:uppercase}
.addr .row span{font-size:14px;font-weight:500;color:var(--ink)}
.form{top:2568px;left:500px;width:590px;display:grid;grid-template-columns:1fr 1fr;gap:14px}
.field{background:var(--white);height:54px;border-radius:4px;font-size:14px;color:#555;padding:16px 12px;box-shadow:0 1px 3px rgba(0,0,0,.05)}
.field.msg{grid-column:1/3;height:122px}
.submit{top:2818px;left:500px}

/* footer */
.footer-bg{top:2880px;left:0;width:1200px;height:488px}
.footer{top:3030px;left:0;width:1200px;text-align:center;color:var(--white)}
.footer .brand{justify-content:center;color:var(--white);font-size:56px}
.footer .brand i{width:40px;height:40px}
.footer .links{display:flex;justify-content:center;gap:60px;margin-top:70px;font-size:15px;font-weight:600}
.footer .social{display:flex;justify-content:center;gap:18px;margin-top:36px}
.footer .social b{width:32px;height:32px;border-radius:50%;background:var(--olive)}
.footer .copy{margin-top:34px;font-size:13px;color:#cfcfcf}
</style>
</head>
<body>
<div class="page">

  <!-- hero -->
  <div class="abs hero-photo" role="img" aria-label="Photo of a smiling woman training on a gym machine with her coach"></div>
  <svg class="abs" style="top:560px;left:0" width="1200" height="120" viewBox="0 0 1200 120">
    <path d="M0 40 Q600 110 1200 40 L1200 120 L0 120 Z" fill="#ffffff"/>
    <path d="M0 40 Q600 110 1200 40" fill="none" stroke="#7b8c12" stroke-width="6"/>
  </svg>

  <div class="abs topbar">
    <div class="follow-wrap"><span class="follow">Follow Us On:</span><i class="soc"></i><i class="soc"></i><i class="soc"></i><i class="soc"></i></div>
    <div class="info">
      <span><i class="icon-dot"><svg width="14" height="14" viewBox="0 0 24 24"><path d="M6.6 10.8a15 15 0 006.6 6.6l2.2-2.2a1 1 0 011-.25 11 11 0 003.6.6 1 1 0 011 1V20a1 1 0 01-1 1A17 17 0 013 4a1 1 0 011-1h3.5a1 1 0 011 1 11 11 0 00.6 3.6 1 1 0 01-.25 1z" fill="#fff"/></svg></i>+1 555 014 2290</span>
      <span><i class="icon-dot"><svg width="14" height="14" viewBox="0 0 24 24"><path d="M3 5h18v14H3z" fill="none" stroke="#fff" stroke-width="2"/><path d="M3 6l9 7 9-7" fill="none" stroke="#fff" stroke-width="2"/></svg></i>info@orbifit.com</span>
      <span><i class="icon-dot"><svg width="14" height="14" viewBox="0 0 24 24"><path d="M12 2a7 7 0 00-7 7c0 5 7 13 7 13s7-8 7-13a7 7 0 00-7-7zm0 9.5A2.5 2.5 0 1112 6.5a2.5 2.5 0 010 5z" fill="#fff"/></svg></i>Orbifit, United States</span>
    </div>
  </div>

  <nav class="abs nav">
    <div class="brand"><i></i>Orbifit</div>
    <div class="menu">
      <span class="active">Home</span><span>About Us</span><span>Services</span><span>Testimonials</span><span>Blog</span><span class="cta">Contact Us</span>
    </div>
  </nav>

  <section class="abs hero-copy">
    <div class="eyebrow">WELCOME TO</div>
    <h1 class="heading">Orbifit</h1>
    <p>Itaque earum rerum hic tenetur a sapiente delectus ut aut reiciendis voluptatibus maiores.</p>
    <span class="btn btn-olive">Get Started</span>
    <div class="dots"><b class="on"></b><b></b><b></b></div>
  </section>

  <!-- services -->
  <section class="abs services">
    <div class="mark"></div>
    <h2 class="heading">Our Services</h2>
  </section>
  <div class="svc svc-side" style="left:112px;background:linear-gradient(160deg,#c9a68a,#5d4a3a)" role="img" aria-label="Photo of a woman preparing a healthy meal"></div>
  <div class="svc-label" style="left:112px">Diet Coaching</div>
  <div class="svc svc-main" role="img" aria-label="Photo of a coach training a client with weights">
    <div class="cap">
      <h3>In-Person Coaching</h3>
      <p>Nemo enim ipsam voluptatem quia voluptas sit aspernatur aut odit aut fugit.</p>
      <a>View More</a>
    </div>
  </div>
  <div class="svc svc-side" style="left:820px;background:linear-gradient(160deg,#cfd6dc,#5a6470)" role="img" aria-label="Photo of a coach working at a laptop"></div>
  <div class="svc-label" style="left:820px">Remote Coaching</div>

  <!-- about -->
  <svg class="abs about-bg" width="1200" height="640" viewBox="0 0 1200 640">
    <path d="M0 40 Q600 -20 1200 40 L1200 580 Q600 650 0 580 Z" fill="#1f1f1f"/>
    <path d="M0 40 Q600 -20 1200 40" fill="none" stroke="#7b8c12" stroke-width="6"/>
    <path d="M0 580 Q600 650 1200 580" fill="none" stroke="#7b8c12" stroke-width="6"/>
  </svg>
  <div class="abs about-flag" role="img" aria-label="Illustration of a flag held by the mascot"></div>
  <div class="abs about-art" role="img" aria-label="Illustration of an astronaut mascot planting a flag"></div>
  <section class="abs about-copy">
    <div class="mark"></div>
    <h2 class="heading">About Orbifit</h2>
    <p>Nam libero tempore, cum soluta nobis est eligendi optio cumque nihil impedit quo minus id quod maxime placeat facere possimus, omnis voluptas assumenda est, omnis dolor repellendus.</p>
    <p>Temporibus autem quibusdam et aut officiis debitis aut rerum necessitatibus saepe eveniet ut et voluptates repudiandae sint et molestiae non recusandae itaque earum rerum hic tenetur.</p>
    <span class="btn btn-white">Read More</span>
  </section>

  <!-- testimonials -->
  <section class="abs reviews">
    <div class="mark"></div>
    <h2 class="heading">What Customer Says</h2>
  </section>
  <div class="avatar av-left" role="img" aria-label="Portrait of a customer"></div>
  <div class="avatar av-right" role="img" aria-label="Portrait of a customer"></div>
  <div class="avatar av-main" role="img" aria-label="Portrait of the reviewing customer"></div>
  <i class="dot-red" style="top:2058px;left:364px"></i>
  <i class="dot-red" style="top:2000px;left:880px;width:8px;height:8px"></i>
  <div class="quote" style="top:2080px;left:140px">“</div>
  <div class="quote" style="top:2160px;left:920px">”</div>
  <div class="review-body">
    <div class="name">Daniel Verro</div>
    <div class="loc">United States</div>
    <div class="stars">
      <svg width="22" height="22" viewBox="0 0 24 24"><path d="M12 2l3 7 7 .6-5.3 4.6 1.6 7.2L12 17.6 5.7 21.4l1.6-7.2L2 9.6 9 9z" fill="#f2a516"/></svg>
      <svg width="22" height="22" viewBox="0 0 24 24"><path d="M12 2l3 7 7 .6-5.3 4.6 1.6 7.2L12 17.6 5.7 21.4l1.6-7.2L2 9.6 9 9z" fill="#f2a516"/></svg>
      <svg width="22" height="22" viewBox="0 0 24 24"><path d="M12 2l3 7 7 .6-5.3 4.6 1.6 7.2L12 17.6 5.7 21.4l1.6-7.2L2 9.6 9 9z" fill="#f2a516"/></svg>
      <svg width="22" height="22" viewBox="0 0 24 24"><path d="M12 2l3 7 7 .6-5.3 4.6 1.6 7.2L12 17.6 5.7 21.4l1.6-7.2L2 9.6 9 9z" fill="#f2a516"/></svg>
      <svg width="22" height="22" viewBox="0 0 24 24"><path d="M12 2l3 7 7 .6-5.3 4.6 1.6 7.2L12 17.6 5.7 21.4l1.6-7.2L2 9.6 9 9z" fill="#f2a516"/></svg>
    </div>
    <p>Itaque earum rerum hic tenetur a sapiente delectus, ut aut reiciendis voluptatibus maiores alias consequatur aut perferendis doloribus asperiores repellat. Et harum quidem rerum facilis est et expedita distinctio nam libero tempore.</p>
  </div>
  <div class="rv-dots"><div class="dots" style="margin:0"><b></b><b class="on"></b><b></b><b></b></div></div>

  <!-- contact -->
  <svg class="abs contact-bg" width="1200" height="600" viewBox="0 0 1200 600">
    <path d="M0 20 Q600 90 1200 20 L1200 600 L0 600 Z" fill="#f1f1f1"/>
  </svg>
  <section class="abs contact-head">
    <div class="mark"></div>
    <h2 class="heading">Get In Touch With Us</h2>
  </section>
  <div class="abs addr">
    <h4>ADDRESS</h4>
    <div class="row"><i class="icon-dot"><svg width="18" height="18" viewBox="0 0 24 24"><path d="M12 2a7 7 0 00-7 7c0 5 7 13 7 13s7-8 7-13a7 7 0 00-7-7zm0 9.5A2.5 2.5 0 1112 6.5a2.5 2.5 0 010 5z" fill="#fff"/></svg></i><div><strong>Location</strong><span>Orbifit, United States</span></div></div>
    <div class="row"><i class="icon-dot"><svg width="18" height="18" viewBox="0 0 24 24"><path d="M6.6 10.8a15 15 0 006.6 6.6l2.2-2.2a1 1 0 011-.25 11 11 0 003.6.6 1 1 0 011 1V20a1 1 0 01-1 1A17 17 0 013 4a1 1 0 011-1h3.5a1 1 0 011 1 11 11 0 00.6 3.6 1 1 0 01-.25 1z" fill="#fff"/></svg></i><div><strong>Phone Number</strong><span>+1 555 014 2290</span></div></div>
    <div class="row"><i class="icon-dot"><svg width="18" height="18" viewBox="0 0 24 24"><path d="M3 5h18v14H3z" fill="none" stroke="#fff" stroke-width="2"/><path d="M3 6l9 7 9-7" fill="none" stroke="#fff" stroke-width="2"/></svg></i><div><strong>Email Address</strong><span>info@orbifit.com</span></div></div>
  </div>
  <form class="abs form">
    <div class="field">First Name</div>
    <div class="field">Last Name</div>
    <div class="field">Your Phone</div>
    <div class="field">Your Email</div>
    <div class="field msg">Message</div>
  </form>
  <span class="abs btn btn-olive submit">Submit</span>

  <!-- footer -->
  <svg class="abs footer-bg" width="1200" height="488" viewBox="0 0 1200 488">
    <path d="M0 60 Q600 -10 1200 60 L1200 488 L0 488 Z" fill="#1f1f1f"/>
    <path d="M0 60 Q600 -10 1200 60" fill="none" stroke="#7b8c12" stroke-width="6"/>
  </svg>
  <footer class="abs footer">
    <div class="brand"><i></i>Orbifit</div>
    <div class="links"><span>Home</span><span>About Us</span><span>Services</span><span>Testimonials</span><span>Blog</span><span>Contact Us</span></div>
    <div class="social"><b></b><b></b><b></b><b></b></div>
    <div class="copy">Copyright@2023 Orbifit All Rights Reserved</div>
  </footer>

</div>
</body>
</html>
```